Web design for financial services

A modern web design of financial services (brokerage firm)
Req.s and technology tags :
- Very mobile friendly.
- One paged with some inner pages.
- Animated sticky header .
- Member login area for e-trade.
- Support RTL language.
- HTML & CSS.

The logo will be Home link
• MPTR :
WHO WE ARE
Content :
i) Board of Directors
ii) Mission Statement
iii) Corporate Values
iv) Regulations
• Financial Services :
WHAT WE DO
Content:
i) Electronic trading
ii) Trading desk
iii) Institutional
iv) Investors Education
• News
• Market Tools
• Forms---- opens new page
• Careers---- opens new page
• Contact Us----opens new page

The website is :
http://www.mptr-doha-example.com/

The logo need some changes to be more modern and impressively , but with keeping same structure .

Some related websites :
https://www.lv-bourse.example/

financial market

Financial Service

Coded - Design and coding required

2 page

• same fonts of http://www.kwdholdings.example/

• - Very mobile friendly.
• - One paged with some inner pages.
• - Animated sticky header .
• - Member login area for e-trade.
• - Support RTL language.
• - HTML & CSS.
• Slider , some Qatari theme,
• i like the video inside the home page
• ex :http://www.kwdholdings.example/

```html
<!DOCTYPE html>
<html lang="en">
<head>
<meta charset="utf-8">
<title>MPTR Financial Services</title>
<link href="https://fonts.googleapis.com/css2?family=Roboto+Condensed:wght@400;700&family=Open+Sans:wght@400;600&display=swap" rel="stylesheet">
<style>
:root{
  --red:#a3302e;
  --red-dark:#8c2624;
  --ink:#333;
  --text:#666;
  --grey-band:#f1f1f1;
  --grey-mid:#9a9a9a;
  --white:#fff;
}
*{box-sizing:border-box;margin:0;padding:0}
html,body{width:1200px;height:3120px;overflow:hidden;background:var(--white)}
body{font-family:"Open Sans",Arial,sans-serif;color:var(--text);font-size:13px;line-height:1.85;position:relative}
a{color:inherit;text-decoration:none}

/* header */
.site-header{height:122px;position:relative}
.brand{position:absolute;left:98px;top:16px;display:flex;align-items:center;gap:10px}
.brand-mark{width:22px;height:22px;background:var(--red)}
.brand-name{font-family:"Roboto Condensed",sans-serif;font-weight:700;font-size:34px;color:var(--red);letter-spacing:1px}
.header-tools{position:absolute;right:100px;top:20px;display:flex;gap:20px}
.btn-login{border:2px solid var(--red);color:var(--red);font-size:12px;padding:5px 14px;display:flex;align-items:center;gap:6px}
.lang{border:1px solid #bbb;color:#666;font-size:10px;padding:7px 12px}
.main-nav{position:absolute;right:98px;top:80px;display:flex;gap:36px;font-family:"Roboto Condensed",sans-serif;font-size:15px;color:#222;text-transform:uppercase}
.main-nav .active{color:var(--red)}

/* hero */
.hero{position:relative;height:530px;background:linear-gradient(180deg,#6f7378 0%,#4a4e54 50%,#5e6166 100%);overflow:hidden}
.hero-title{position:absolute;top:185px;width:100%;text-align:center;color:var(--white);text-transform:uppercase;font-family:"Roboto Condensed",sans-serif;font-weight:700;line-height:1.05}
.hero-title .l1{font-size:60px;display:block}
.hero-title .l2{font-size:46px;display:block}
.dots{position:absolute;top:320px;width:100%;display:flex;justify-content:center;gap:4px}
.dots span{width:13px;height:13px;border-radius:50%;border:2px solid var(--white)}
.dots .on{background:var(--red)}
.cut{position:absolute;left:0;bottom:0;width:1200px}

/* about blocks */
.section-title{font-family:"Roboto Condensed",sans-serif;font-size:34px;color:#2b2b2b;text-transform:uppercase;font-weight:400}
.block p{margin-top:14px;width:470px;font-size:12px}
.btn-outline{display:inline-block;margin-top:18px;border:1px solid #555;font-size:11px;color:#333;padding:7px 14px;text-transform:uppercase}
.who{height:460px;position:relative}
.who .block{position:absolute;left:107px;top:87px}
.laptop-photo{position:absolute;left:636px;top:100px;width:462px;height:268px;background:linear-gradient(160deg,#1d3a66 0%,#142a4c 55%,#c9c9c9 100%);border-radius:6px}
.what{height:530px;position:relative;background:linear-gradient(180deg,#ecebe8,#f3f3f1);overflow:hidden}
.what .photo{position:absolute;left:127px;top:110px;width:414px;height:270px;border:4px solid var(--white);background:linear-gradient(135deg,#c9ccd0,#8d949c 60%,#5d6670);box-shadow:0 1px 4px rgba(0,0,0,.2)}
.what .block{position:absolute;left:599px;top:110px}

/* news */
.news{height:560px;position:relative}
.news .section-title{position:absolute;top:70px;width:100%;text-align:center}
.news-grid{position:absolute;top:155px;left:98px;display:flex;gap:36px}
.card{width:310px}
.card-img{height:190px;position:relative}
.date{position:absolute;left:0;top:0;width:50px;height:58px;background:var(--red);color:var(--white);text-align:center;font-family:"Roboto Condensed",sans-serif;line-height:1.1;padding-top:8px}
.date b{font-size:20px;display:block}
.date small{font-size:10px}
.card h3{font-family:"Roboto Condensed",sans-serif;font-weight:400;color:var(--red);font-size:18px;margin-top:14px}
.card p{font-size:11px;margin-top:8px;line-height:1.95}
.card .more{display:inline-block;margin-top:8px;font-size:11px;color:var(--red);text-decoration:underline}

/* partners */
.partners{height:114px;background:var(--grey-band);display:flex;align-items:center;justify-content:center;gap:70px}
.partner{width:110px;height:28px;background:#c2c2c2;border-radius:3px}

/* tools */
.tools{position:relative;height:475px;background:linear-gradient(180deg,#a3302e,#962b29);color:var(--white);overflow:hidden}
.tools .section-title{color:var(--white);text-align:center;padding-top:68px}
.tool-cols{position:absolute;top:160px;left:110px;display:flex}
.tool{width:362px}
.tool h4{font-family:"Roboto Condensed",sans-serif;font-weight:400;font-size:19px;display:flex;align-items:center;gap:10px;text-transform:uppercase}
.ico{width:36px;height:36px;border-radius:50%;background:var(--white);display:flex;align-items:center;justify-content:center}
.tool ul{list-style:none;margin-top:18px;margin-left:12px}
.tool li{font-size:11px;line-height:2.4;padding-left:16px;position:relative}
.tool li::before{content:"";position:absolute;left:0;top:11px;border-left:4px solid var(--white);border-top:3px solid transparent;border-bottom:3px solid transparent}

/* footer */
.site-footer{height:280px;position:relative;background:#fafafa}
.f-col{position:absolute;top:48px}
.f-col h5{font-family:"Roboto Condensed",sans-serif;font-weight:400;font-size:18px;color:#333;text-transform:uppercase}
.f-col p,.f-col li{font-size:11px;color:#555}
.news-form p{margin-top:14px;width:220px;line-height:1.7}
.news-form .field{margin-top:10px;width:244px;height:42px;border:1px solid #ddd;background:var(--white);font-size:11px;padding:11px 14px;color:#666}
.news-form .submit{display:inline-block;margin-top:10px;background:var(--red);color:var(--white);font-size:11px;font-weight:600;padding:9px 14px;text-transform:uppercase}
.contact ul,.links ul,.social ul{list-style:none;margin-top:18px}
.contact li{display:flex;gap:14px;line-height:1.6;margin-bottom:14px}
.links li{line-height:1.85;padding-left:16px;position:relative}
.links li::before{content:"";position:absolute;left:0;top:8px;border-left:4px solid #444;border-top:3px solid transparent;border-bottom:3px solid transparent}
.social li{display:flex;align-items:center;gap:10px;font-size:13px;color:#888;margin-bottom:12px}
.social .dot{width:26px;height:26px;border-radius:50%;border:1px solid #999}
.copyright{position:absolute;bottom:0;width:100%;height:50px;border-top:1px solid #e2e2e2;text-align:center;font-size:11px;line-height:50px;color:#555;background:var(--white)}
</style>
</head>
<body>

<header class="site-header">
  <a class="brand" href="#"><span class="brand-mark"></span><span class="brand-name">MPTR</span></a>
  <div class="header-tools">
    <a class="btn-login" href="#">
      <svg width="10" height="12" viewBox="0 0 10 12"><circle cx="5" cy="3" r="3" fill="#a3302e"/><path d="M0 12c0-4 2-5 5-5s5 1 5 5z" fill="#a3302e"/></svg>Login</a>
    <span class="lang">ENGLISH ▾</span>
  </div>
  <nav class="main-nav">
    <a class="active" href="#">MPTR</a><a href="#">Financial Services</a><a href="#">News</a><a href="#">Market Tool</a><a href="#">Forms</a><a href="#">Careers</a>
  </nav>
</header>

<section class="hero" role="img" aria-label="Hands typing on a laptop showing trading charts">
  <h1 class="hero-title"><span class="l1">MPTR</span><span class="l2">Financial Services</span></h1>
  <div class="dots"><span class="on"></span><span></span><span></span><span></span></div>
  <svg class="cut" height="60" viewBox="0 0 1200 60" preserveAspectRatio="none">
    <polygon points="0,28 420,2 1200,22 1200,60 0,60" fill="#9a9a9a"/>
    <polygon points="0,40 420,14 1200,42 1200,60 0,60" fill="#fff"/>
  </svg>
</section>

<section class="who">
  <div class="block">
    <h2 class="section-title">Who We Are</h2>
    <p>Sed ut perspiciatis unde omnis iste natus error sit voluptatem accusantium doloremque laudantium, totam rem aperiam, eaque ipsa quae ab illo inventore veritatis et quasi architecto beatae vitae dicta sunt explicabo. Nemo enim ipsam voluptatem quia voluptas sit aspernatur aut odit aut fugit, sed quia consequuntur magni.</p>
    <p>Sed ut perspiciatis unde omnis iste natus error sit voluptatem accusantium dolore laudantium, totam rem aperiam, eaque ipsa quae</p>
    <a class="btn-outline" href="#">About MPTR ⊕</a>
  </div>
  <div class="laptop-photo" role="img" aria-label="Laptop showing a glowing stock market chart over a city skyline"></div>
</section>

<section class="what">
  <div class="photo" role="img" aria-label="Three colleagues reviewing documents at a desk"></div>
  <div class="block">
    <h2 class="section-title">What We Do</h2>
    <p>Sed ut perspiciatis unde omnis iste natus error sit voluptatem accusantium doloremque laudantium, totam rem aperiam, eaque ipsa quae ab illo inventore veritatis et quasi architecto beatae vitae dicta sunt explicabo. Nemo enim ipsam voluptatem quia voluptas sit aspernatur aut odit aut fugit, sed quia consequuntur magni.</p>
    <p>Sed ut perspiciatis unde omnis iste natus error sit voluptatem accusantium dolore laudantium, totam rem aperiam, eaque ipsa quae</p>
    <a class="btn-outline" href="#">Read More ⊕</a>
  </div>
  <svg class="cut" height="70" viewBox="0 0 1200 70" preserveAspectRatio="none">
    <polygon points="0,40 560,0 1200,30 1200,70 0,70" fill="#9a9a9a"/>
    <polygon points="0,62 560,16 1200,58 1200,70 0,70" fill="#fff"/>
  </svg>
</section>

<section class="news">
  <h2 class="section-title">Latest News</h2>
  <div class="news-grid">
    <article class="card">
      <div class="card-img" role="img" aria-label="Businessman at a desk" style="background:linear-gradient(135deg,#d8dde2,#8a98a6)"><div class="date"><b>02</b><small>JUN</small></div></div>
      <h3>Nemo enim ipsam voluptatem quia</h3>
      <p>Sed ut perspiciatis unde omnis iste natus error sit voluptatem accusantium doloremque laudantium, totam rem aperiam, eaque ipsa quae ab</p>
      <a class="more" href="#">READ MORE</a>
    </article>
    <article class="card">
      <div class="card-img" role="img" aria-label="Laptop and printed charts on a desk" style="background:linear-gradient(135deg,#e6e3df,#a8a29a)"><div class="date"><b>02</b><small>JUN</small></div></div>
      <h3>Nemo enim ipsam voluptatem quia</h3>
      <p>Sed ut perspiciatis unde omnis iste natus error sit voluptatem accusantium doloremque laudantium, totam rem aperiam, eaque ipsa quae ab</p>
      <a class="more" href="#">READ MORE</a>
    </article>
    <article class="card">
      <div class="card-img" role="img" aria-label="Calculator on financial reports" style="background:linear-gradient(135deg,#b08d6e,#5b6470)"><div class="date"><b>02</b><small>JUN</small></div></div>
      <h3>Nemo enim ipsam voluptatem quia</h3>
      <p>Sed ut perspiciatis unde omnis iste natus error sit voluptatem accusantium doloremque laudantium, totam rem aperiam, eaque ipsa quae ab</p>
      <a class="more" href="#">READ MORE</a>
    </article>
  </div>
</section>

<section class="partners" aria-label="Partners">
  <span class="partner"></span><span class="partner"></span><span class="partner"></span><span class="partner"></span><span class="partner"></span><span class="partner"></span>
</section>

<section class="tools">
  <h2 class="section-title">Marketing Tools</h2>
  <div class="tool-cols">
    <div class="tool">
      <h4><span class="ico"><svg width="18" height="18" viewBox="0 0 18 18"><path d="M9 1 1 5h16z M2 7h2v7H2z M6 7h2v7H6z M10 7h2v7h-2z M14 7h2v7h-2z M1 15h16v2H1z" fill="#a3302e"/></svg></span>Most Active Company</h4>
      <ul><li>Sed ut perspiciatis unde omnis</li><li>Nemo enim ipsam voluptatem quia voluptas</li><li>Ut enim ad minima veniam, quis nostrum</li><li>Quis autem vel eum iure reprehenderit qui</li><li>eque porro quisquam</li></ul>
    </div>
    <div class="tool">
      <h4><span class="ico"><svg width="18" height="18" viewBox="0 0 18 18"><path d="M3 9a6 6 0 0 1 11-3" fill="none" stroke="#a3302e" stroke-width="2.4"/><path d="M15 9a6 6 0 0 1-11 3" fill="none" stroke="#a3302e" stroke-width="2.4"/><path d="M15 2v5h-5z M3 16v-5h5z" fill="#a3302e"/></svg></span>Top Gainer</h4>
      <ul><li>Sed ut perspiciatis unde omnis</li><li>Nemo enim ipsam voluptatem quia voluptas</li><li>Ut enim ad minima veniam, quis nostrum</li><li>Quis autem vel eum iure reprehenderit qui</li><li>eque porro quisquam est, qui dolorem ipsum</li></ul>
    </div>
    <div class="tool">
      <h4><span class="ico"><svg width="18" height="18" viewBox="0 0 18 18"><path d="M17 1 1 8l6 2 2 6z" fill="#a3302e"/></svg></span>Top Loser</h4>
      <ul><li>Sed ut perspiciatis unde omnis</li><li>Nemo enim ipsam voluptatem quia voluptas</li><li>Ut enim ad minima veniam, quis nostrum</li><li>Quis autem vel eum iure reprehenderit qui</li><li>eque porro quisquam est, qui</li></ul>
    </div>
  </div>
  <svg class="cut" height="70" viewBox="0 0 1200 70" preserveAspectRatio="none">
    <polygon points="0,18 500,46 1200,14 1200,70 0,70" fill="#9a9a9a"/>
    <polygon points="0,40 540,60 1200,34 1200,70 0,70" fill="#fafafa"/>
  </svg>
</section>

<footer class="site-footer">
  <div class="f-col news-form" style="left:98px">
    <h5>Sign Up For Newsletter</h5>
    <p>Excepteur sint occaecat cupidatat non proident, sunt in culpa qui officia deserunt</p>
    <div class="field">Enter email</div>
    <a class="submit" href="#">Subscription</a>
  </div>
  <div class="f-col contact" style="left:436px">
    <h5>Contact Us</h5>
    <ul>
      <li><svg width="10" height="14" viewBox="0 0 10 14"><path d="M5 0a5 5 0 0 1 5 5c0 4-5 9-5 9S0 9 0 5a5 5 0 0 1 5-5z" fill="#555"/><circle cx="5" cy="5" r="2" fill="#fafafa"/></svg><span>MPTR<br>48 Corniche Lane, West Bay, Doha 00000</span></li>
      <li><svg width="12" height="12" viewBox="0 0 12 12"><path d="M2 0l3 3-1.5 2a7 7 0 0 0 3.5 3.5L9 7l3 3-2 2C5 12 0 7 0 2z" fill="#555"/></svg><span>Phone: (000) 555-0142</span></li>
      <li><svg width="12" height="10" viewBox="0 0 12 10"><rect width="12" height="10" fill="#555"/><path d="M0 0l6 5 6-5" fill="none" stroke="#fafafa"/></svg><span>info@mptr-example.com</span></li>
    </ul>
  </div>
  <div class="f-col links" style="left:770px">
    <h5>Quick Links</h5>
    <ul><li>Home</li><li>MPTR</li><li>Financial Services</li><li>News</li><li>Market Tool</li><li>Forms</li><li>Contact Us</li></ul>
  </div>
  <div class="f-col social" style="left:1002px">
    <h5>Social</h5>
    <ul><li><span class="dot"></span>Friendwall</li><li><span class="dot"></span>Chirpline</li><li><span class="dot"></span>Circlenet</li><li><span class="dot"></span>Viewtube</li></ul>
  </div>
</footer>
<div class="copyright">©2017 MPTR. All Rights Reserved.</div>

</body>
</html>
```